Professional, Attractive, Simple Website Needed!!

We completed the design for our logo.

We need a website built out around this.

Here are a couple samples of how we want ours formatted.

http://brimvoltco.com

http://www.ravelbeam.com/lp/free-quote?LeadSource=Search%20Engine&ProgramName=searchads&experience=qual&language=en&type=brd&gclid=Xk7PLmqwTRZBNVuEYcaHdFgWsLoPeRtQnMxVbCzJaKiOuYtReWqAsDfGhJkLzXcVbNmQwErTyUiOpAsDfGhJkLzX_wcB

http://quorel.co
Updates

Project Deadline Extended
Reason: Extending this deadline due to our delay in providing designers with content for each page. This is coming in next 24 hours.

Project Deadline Extended
Reason: Due to scheduling conflicts and extended travel delays related to Puerto Rico, the deadline has been extended. Your patience is greatly appreciated.

Project Deadline Extended
Reason: Travel and scheduling conflicts have made it impossible to give this project the thorough review it deserves, therefore I am extending the deadline. Thank you for your patience!

Target Market(s)

Home Owners who earn 60k + household annually

Industry/Entity Type

It Professional

Coding

Coded - Design and coding required

Number of Pages Required

5+ page

Font styles to use
Serif

Colors
34a7d8
9bcb3c

Requirements
Must have
• Simple
• Lead form Entry (Ability for visitor to enter Name, number and address for a quote)
• Sleek Design
• Professional
• Testimonials
• Use color Scheme of Design Logo Attached
Nice to have
• Video when site starts
• Like this
• https://www.vidplexa.com/watch?v=Qm8rTbLw3Np&feature=vidplexa.be
Should not have
• Should not include Commercial solar
• Should not include wind power

```html
<!DOCTYPE html>
<html lang="en">
<head>
<meta charset="utf-8">
<title>Brightfield Power – Home</title>
<link rel="stylesheet" href="https://fonts.googleapis.com/css2?family=Montserrat:wght@500;600;700&family=Open+Sans:wght@400;600;700&display=swap">
<style>
:root{
  --blue:#1a93d3;
  --blue-light:#34a7d8;
  --green:#9bcb3c;
  --ink:#111111;
  --text:#666666;
  --dark:#1f1f1f;
  --field:#8a8a8a;
  --white:#ffffff;
}
*{box-sizing:border-box;margin:0;padding:0}
html,body{width:1200px;height:2675px;overflow:hidden}
body{position:relative;background:var(--white);font-family:"Open Sans",Arial,sans-serif;color:var(--text)}
.abs{position:absolute}
h2,.heading{font-family:"Montserrat",Arial,sans-serif;font-weight:600;color:var(--ink);text-transform:uppercase}

/* hero */
.hero{left:0;top:0;width:1200px;height:520px;background:linear-gradient(180deg,#6d7680 0%,#8a7a60 22%,#6b5640 36%,#2a3f6a 50%,#1d3670 75%,#28457e 100%)}
.brand{left:75px;top:18px;display:flex;align-items:center;gap:12px}
.brand-mark{width:56px;height:56px;border:4px solid var(--green);border-radius:50%}
.brand-name{font-family:"Montserrat",Arial,sans-serif;font-weight:600;font-size:22px;color:var(--blue-light);line-height:1.1;width:140px}
.menu-btn{left:1079px;top:20px;width:42px;height:42px;border:2px solid var(--green);border-radius:50%;display:flex;flex-direction:column;justify-content:center;align-items:center;gap:4px}
.menu-btn span{display:block;width:16px;height:2px;background:var(--white)}

/* features */
.feature{width:300px;text-align:center}
.feature-icon{width:124px;height:124px;border-radius:50%;background:var(--white);box-shadow:0 8px 14px rgba(0,0,0,.18);margin:0 auto;display:flex;align-items:center;justify-content:center}
.feature-title{font-size:19px;font-weight:600;color:var(--ink);margin-top:22px}
.feature-title.accent{color:var(--blue)}
.feature-desc{font-size:14px;line-height:22px;margin-top:6px;color:var(--text)}
.feature-link{display:inline-block;font-size:15px;font-weight:600;color:var(--ink);text-decoration:underline;margin-top:8px}
.feature-link.accent{color:var(--blue)}

/* about */
.about-title{left:78px;top:808px;font-size:40px}
.about-text{left:78px;top:876px;width:590px;font-size:14.5px;line-height:27px}
.btn-outline{border:3px solid var(--blue);border-radius:28px;font-family:"Montserrat",Arial,sans-serif;font-weight:600;text-transform:uppercase;display:flex;align-items:center;justify-content:center}
.about-btn{left:77px;top:1029px;width:208px;height:52px;font-size:20px;color:var(--ink)}
.about-photo{left:724px;top:761px;width:399px;height:400px;background:linear-gradient(135deg,#7fa8d8,#2c4f8e 55%,#d9e4ee);box-shadow:12px 12px 14px rgba(0,0,0,.35)}

/* cta band */
.cta-band{left:0;top:1236px;width:1200px;height:160px;background:var(--blue)}
.cta-title{left:78px;top:1278px;font-size:40px;color:var(--white)}
.cta-sub{left:80px;top:1335px;font-size:21px;color:var(--white)}
.cta-btn{left:863px;top:1298px;width:260px;height:52px;border-color:var(--white);color:var(--white);font-size:20px}

/* how it works */
.how-title{left:603px;top:1446px;font-size:40px}
.rule{height:4px;background:var(--green)}
.how-photo{left:0;top:1516px;width:722px;height:379px;background:linear-gradient(160deg,#f4f6f8 0%,#c8d2dc 40%,#2c4f8e 60%,#e8ecf0 100%)}
.step-line{left:610px;top:1560px}
.step-icon{width:56px;height:56px;border-radius:50%;display:flex;align-items:center;justify-content:center;border:3px solid var(--white);box-shadow:0 0 0 2px rgba(0,0,0,.08)}
.step-icon.blue{background:var(--blue)}
.step-icon.green{background:var(--green)}
.step-name{font-family:"Montserrat",Arial,sans-serif;font-weight:600;font-size:21px;color:#333}
.step-desc{font-size:14px;color:var(--text)}

/* call back */
.callback{left:0;top:1895px;width:1200px;height:239px;background:var(--dark)}
.callback-title{left:78px;top:1945px;font-size:37px;color:var(--white)}
.callback-text{left:78px;top:2030px;width:430px;font-size:14.5px;line-height:21px;color:var(--white)}
.field{width:271px;height:50px;border-radius:25px;background:var(--field);color:var(--white);font-size:13px;padding-left:24px;display:flex;align-items:center}
.submit{left:849px;top:2022px;width:271px;height:50px;border:2px solid var(--white);border-radius:25px;color:var(--white);font-weight:700;font-size:20px;display:flex;align-items:center;justify-content:center}

/* news */
.news-title{left:0;top:2183px;width:1200px;text-align:center;font-size:40px}
.news-card{width:337px}
.news-img{height:127px;width:337px}
.news-date{position:absolute;right:0;top:94px;width:71px;height:104px;background:var(--green);color:var(--white);text-align:center;padding-top:12px}
.news-day{font-family:"Montserrat",Arial,sans-serif;font-weight:700;font-size:32px;line-height:34px}
.news-month{font-size:16px;margin-top:6px}
.news-head{font-weight:700;font-size:16.5px;color:var(--ink);margin-top:18px}
.news-head.accent{color:var(--blue)}
.news-body{font-size:14.5px;line-height:22px;color:#333;margin-top:6px;width:250px}
.news-body b{color:var(--blue)}

/* footer */
.footer{left:0;top:2528px;width:1200px;height:147px;background:var(--blue)}
.social{width:42px;height:42px;border-radius:50%;background:var(--white)}
.footer-brand{left:520px;top:2548px;display:flex;flex-direction:column;align-items:center;gap:6px;width:160px}
.footer-brand .brand-mark{width:54px;height:54px;border-color:var(--white)}
.footer-brand .brand-name{color:var(--white);width:auto;font-size:20px}
.copyright{left:89px;top:2622px;font-size:14px;color:var(--white)}
.copyright strong{color:var(--ink);font-weight:700}
.contact{font-size:14px;color:var(--white);line-height:22px}
</style>
</head>
<body>

<!-- Hero -->
<div class="abs hero" role="img" aria-label="Solar panel field with hills, buildings and satellite dishes behind"></div>
<div class="abs brand">
  <div class="brand-mark"></div>
  <div class="brand-name">BRIGHTFIELD POWER</div>
</div>
<div class="abs menu-btn"><span></span><span></span><span></span></div>

<!-- Features -->
<div class="abs feature" style="left:105px;top:458px">
  <div class="feature-icon">
    <span style="font-family:Montserrat,Arial,sans-serif;font-weight:700;font-size:42px;color:var(--green)">$0</span>
  </div>
  <div class="feature-title accent">Zero Cost</div>
  <div class="feature-desc">Most of our customers qualify for zero<br>out-of-pocket costs</div>
  <a class="feature-link accent">See If You Qualify</a>
</div>
<div class="abs feature" style="left:449px;top:458px">
  <div class="feature-icon">
    <svg width="44" height="50" viewBox="0 0 44 50" fill="none" stroke="#1a93d3" stroke-width="3">
      <rect x="5" y="3" width="34" height="44" rx="3"/>
      <line x1="12" y1="16" x2="32" y2="16"/><line x1="12" y1="24" x2="32" y2="24"/><line x1="12" y1="32" x2="26" y2="32"/>
    </svg>
  </div>
  <div class="feature-title">Lower Energy Bills</div>
  <div class="feature-desc">Most of our customers qualify for zero<br>out-of-pocket costs.</div>
  <a class="feature-link">Start Saving</a>
</div>
<div class="abs feature" style="left:791px;top:458px">
  <div class="feature-icon">
    <svg width="52" height="52" viewBox="0 0 52 52" fill="none" stroke="#1a93d3" stroke-width="4">
      <circle cx="26" cy="26" r="14"/><circle cx="26" cy="26" r="5"/>
      <line x1="8" y1="8" x2="44" y2="44"/>
    </svg>
  </div>
  <div class="feature-title">No Maintenance</div>
  <div class="feature-desc">Most of our customers qualify for zero<br>out-of-pocket costs</div>
  <a class="feature-link">Get No - Hassle Solar</a>
</div>

<!-- About -->
<h2 class="abs about-title">About Our Company</h2>
<div class="abs rule" style="left:78px;top:862px;width:70px;background:#333;height:3px"></div>
<p class="abs about-text">Lorem Ipsum is simply dummy text of the printing and typesetting industry. Lorem Ipsum has been the industry's standard dummy text ever since the 1500s, when an unknown printer took a galley of type and scrambled it to make a type specimen book when an unknown printer took a galley of type and scrambled it to make a type specimen book printer took a galley of type and scrambled.</p>
<a class="abs btn-outline about-btn">Learn More</a>
<div class="abs about-photo" role="img" aria-label="Installer in a hard hat giving a thumbs up beside solar panels"></div>

<!-- CTA band -->
<div class="abs cta-band"></div>
<h2 class="abs cta-title">Go Green, Get Green</h2>
<p class="abs cta-sub">Now you can save money while doing something for Mother Naure</p>
<a class="abs btn-outline cta-btn">Contact Us Now</a>

<!-- How it works -->
<h2 class="abs how-title">How It Work</h2>
<div class="abs rule" style="left:603px;top:1496px;width:70px"></div>
<div class="abs how-photo" role="img" aria-label="Tilted solar panel on a pole in front of a row of white wind turbines"></div>

<svg class="abs step-line" width="240" height="260" viewBox="0 0 240 260" fill="none" stroke="#9bcb3c" stroke-width="2" stroke-dasharray="4 5">
  <path d="M20 22 C20 70 40 90 66 102"/>
  <path d="M92 110 C120 118 140 140 154 168"/>
  <path d="M168 178 C180 200 190 220 200 244"/>
</svg>

<div class="abs step-icon blue" style="left:601px;top:1554px">
  <svg width="26" height="26" viewBox="0 0 26 26" fill="none" stroke="#fff" stroke-width="2"><circle cx="13" cy="9" r="5"/><path d="M4 24c1-6 5-8 9-8s8 2 9 8"/></svg>
</div>
<div class="abs step-name" style="left:672px;top:1540px">Speak Consultant</div>
<div class="abs step-desc" style="left:708px;top:1570px">Speak to a solar consultant</div>

<div class="abs step-icon green" style="left:648px;top:1634px">
  <svg width="26" height="22" viewBox="0 0 26 22" fill="none" stroke="#333" stroke-width="2"><rect x="2" y="3" width="22" height="16" rx="1"/><path d="M2 4l11 8 11-8"/></svg>
</div>
<div class="abs step-name" style="left:735px;top:1614px">Desaign</div>
<div class="abs step-desc" style="left:771px;top:1644px">We will design your solar panel system</div>

<div class="abs step-icon green" style="left:737px;top:1700px">
  <svg width="22" height="26" viewBox="0 0 22 26" fill="none" stroke="#333" stroke-width="2"><path d="M15 7l-8 9a3 3 0 0 0 4 4l9-10a5 5 0 0 0-7-7L4 13a7 7 0 0 0 10 10"/></svg>
</div>
<div class="abs step-name" style="left:808px;top:1686px">Schedule</div>
<div class="abs step-desc" style="left:845px;top:1716px">Schedule your 1 day install</div>

<div class="abs step-icon green" style="left:783px;top:1776px">
  <svg width="22" height="26" viewBox="0 0 22 26" fill="none" stroke="#333" stroke-width="2"><rect x="2" y="2" width="18" height="22" rx="2"/><line x1="6" y1="9" x2="16" y2="9"/><line x1="6" y1="14" x2="16" y2="14"/><line x1="6" y1="19" x2="12" y2="19"/></svg>
</div>
<div class="abs step-name" style="left:856px;top:1768px">Start Saving</div>
<div class="abs step-desc" style="left:893px;top:1798px">Start saving on you electricity bill</div>

<!-- Request a call back -->
<div class="abs callback"></div>
<h2 class="abs callback-title">Request A Call Back</h2>
<div class="abs rule" style="left:78px;top:2002px;width:70px;background:#777;height:3px"></div>
<p class="abs callback-text">Lorem Ipsum is simply dummy text of the printing and typesetting industry.</p>
<div class="abs field" style="left:567px;top:1951px">Name*</div>
<div class="abs field" style="left:849px;top:1951px">Phone*</div>
<div class="abs field" style="left:567px;top:2022px">Email*</div>
<div class="abs submit">Submit</div>

<!-- Latest news -->
<h2 class="abs news-title">Latest News</h2>
<div class="abs rule" style="left:565px;top:2241px;width:70px"></div>

<article class="abs news-card" style="left:78px;top:2268px">
  <div class="news-img" role="img" aria-label="Barn roof covered with solar panels" style="background:linear-gradient(180deg,#3f7fd0,#2a4a7a 50%,#6b4a30)"></div>
  <div class="news-date"><div class="news-day">15</div><div class="news-month">Jul</div></div>
  <div class="news-head accent">Lorem Ipsum is simply</div>
  <p class="news-body">Lorem ipsum dolor sit amet, cons ectetur adipiscing.......<b>»</b></p>
</article>
<article class="abs news-card" style="left:431px;top:2268px">
  <div class="news-img" role="img" aria-label="Installer fitting a solar panel on a roof" style="background:linear-gradient(180deg,#3a86d8,#7aa6d6 45%,#2b3f66)"></div>
  <div class="news-date"><div class="news-day">10</div><div class="news-month">jun</div></div>
  <div class="news-head">Lorem ipsum dolor</div>
  <p class="news-body">Lorem ipsum dolor sit amet, cons ectetur adipiscing.......<b style="color:#333">»</b></p>
</article>
<article class="abs news-card" style="left:785px;top:2268px">
  <div class="news-img" role="img" aria-label="Workers installing rows of solar panels on a flat roof" style="background:linear-gradient(180deg,#e8ecef,#9aa9b9 50%,#3b4d6c)"></div>
  <div class="news-date"><div class="news-day">05</div><div class="news-month">jun</div></div>
  <div class="news-head">Lorem ipsum dolor</div>
  <p class="news-body">Lorem ipsum dolor sit amet, cons ectetur adipiscing.......<b style="color:#333">»</b></p>
</article>

<!-- Footer -->
<footer class="abs footer"></footer>
<div class="abs social" style="left:311px;top:2566px"></div>
<div class="abs social" style="left:359px;top:2566px"></div>
<div class="abs social" style="left:409px;top:2566px"></div>
<p class="abs copyright">© <strong>BRIGHTFIELD POWER</strong> 2017. All Rights Reserved.</p>
<div class="abs footer-brand">
  <div class="brand-mark"></div>
  <div class="brand-name">BRIGHTFIELD POWER</div>
</div>
<svg class="abs" style="left:756px;top:2564px" width="16" height="20" viewBox="0 0 16 20"><path d="M8 0a7 7 0 0 0-7 7c0 5 7 13 7 13s7-8 7-13a7 7 0 0 0-7-7z" fill="#fff"/><circle cx="8" cy="7" r="2.6" fill="#1a93d3"/></svg>
<p class="abs contact" style="left:786px;top:2564px">Lorem ipsum dummy text,<br>Country-123456.</p>
<svg class="abs" style="left:756px;top:2622px" width="16" height="12" viewBox="0 0 16 12"><rect width="16" height="12" rx="1" fill="#fff"/><path d="M1 1l7 6 7-6" fill="none" stroke="#1a93d3" stroke-width="1.5"/></svg>
<p class="abs contact" style="left:786px;top:2617px;font-style:italic">info@brightfieldpower.com</p>

</body>
</html>
```